Business Card design for law firm = Brightvale Australia

We are seeking a new design for our business cards.
We are keeping our logo, which is attached.
We need space for
Name
Title
Address is , which is
Level 7
214 Marlowe Street
Sydney NSW 2047
Phone :
Mobile :
Fax :
Email :
DX :
website www.brightvale-example.com.au

Industry/Entity Type

Law Firm / Banking and Finance

Contact Information for Business Card

We are seeking a new design for our business cards. We are keeping our logo. We need space for Name Title Address is Level 7 214 Marlowe Street Sydney NSW 2047 Phone Mobile Fax Email DX website www.brightvale-example.com.au

Colors
0054AA
0677BA
7BADD7
CADEEF
E8F1F8

Requirements
Must have
• see our website for general feel www.brightvale-example.com.au

```html
<!DOCTYPE html>
<html lang="en">
<head>
<meta charset="utf-8">
<title>Brightvale Australia – Business Card</title>
<link href="https://fonts.googleapis.com/css2?family=EB+Garamond:wght@400&display=swap" rel="stylesheet">
<style>
  :root {
    --backdrop: #2a2a2a;
    --navy: #2d4f96;
    --navy-deep: #2a4a8e;
    --cyan: #0a8fc4;
    --cyan-bar: #0a84b8;
    --paper: #f1f1f1;
    --paper-shade: #e2e2e2;
    --ink: #2b2b2b;
    --light: #ecebe8;
  }
  * { margin: 0; padding: 0; box-sizing: border-box; }
  html, body { width: 1200px; height: 1138px; overflow: hidden; background: var(--backdrop); }
  .canvas { position: relative; width: 1200px; height: 1138px; }

  .card { position: absolute; border-radius: 16px; overflow: hidden; }
  .card-front {
    left: 272px; top: 184px; width: 622px; height: 376px;
    background: linear-gradient(180deg, var(--navy) 0%, var(--navy-deep) 100%);
  }
  .card-back {
    left: 274px; top: 606px; width: 619px; height: 375px;
    background: linear-gradient(180deg, var(--paper) 0%, var(--paper) 60%, var(--paper-shade) 100%);
  }

  .brand { position: absolute; display: flex; align-items: center; gap: 14px; }
  .brand-square { background: var(--cyan); flex: none; }
  .brand-name {
    font-family: "EB Garamond", Georgia, serif; font-weight: 400;
    line-height: 1; white-space: nowrap;
  }

  /* front */
  .card-front .brand { left: 0; width: 100%; justify-content: center; top: 140px; }
  .card-front .brand-square { width: 30px; height: 30px; }
  .card-front .brand-name { font-size: 54px; color: var(--light); }
  .front-url {
    position: absolute; left: 0; width: 100%; top: 332px; text-align: center;
    font-family: "EB Garamond", Georgia, serif; font-size: 14px; letter-spacing: 0.42em; color: var(--light);
  }
  .front-bar { position: absolute; left: 142px; top: 367px; width: 340px; height: 9px; background: var(--cyan-bar); }

  /* back */
  .card-back .brand { right: 35px; top: 90px; gap: 12px; }
  .card-back .brand-square { width: 26px; height: 26px; }
  .card-back .brand-name { font-size: 44px; color: var(--navy); }

  .holder-name { position: absolute; left: 34px; top: 224px; font-family: "EB Garamond", Georgia, serif; font-size: 24px; color: var(--navy); line-height: 1; }
  .holder-title { position: absolute; left: 34px; top: 252px; font-family: "EB Garamond", Georgia, serif; font-size: 16px; color: var(--ink); line-height: 1; }

  .contact { position: absolute; display: flex; align-items: center; gap: 8px; font-family: "EB Garamond", Georgia, serif; font-size: 15px; color: var(--ink); line-height: 1; white-space: nowrap; }
  .contact svg { width: 14px; height: 14px; flex: none; fill: var(--cyan); }
  .address { position: absolute; left: 420px; top: 294px; display: flex; gap: 8px; font-family: "EB Garamond", Georgia, serif; font-size: 15px; color: var(--ink); line-height: 22px; white-space: nowrap; }
  .address svg { width: 13px; height: 16px; margin-top: 3px; fill: var(--cyan); flex: none; }

  .back-bars { position: absolute; left: 0; bottom: 0; width: 100%; height: 20px; display: flex; }
  .back-bars .bar-navy { width: 310px; background: var(--navy); }
  .back-bars .bar-cyan { flex: 1; background: var(--cyan-bar); }
</style>
</head>
<body>
<main class="canvas">

  <section class="card card-front" aria-label="Card front">
    <div class="brand">
      <div class="brand-square"></div>
      <div class="brand-name">Brightvale</div>
    </div>
    <div class="front-url">www.brightvale-example.com.au</div>
    <div class="front-bar"></div>
  </section>

  <section class="card card-back" aria-label="Card back">
    <div class="brand">
      <div class="brand-square"></div>
      <div class="brand-name">Brightvale</div>
    </div>

    <div class="holder-name">Sam Whitford</div>
    <div class="holder-title">Managing Director</div>

    <div class="contact" style="left:34px; top:296px;">
      <svg viewBox="0 0 16 16"><path d="M2 5c0-2 2-3 6-3s6 1 6 3v1h-3V5H5v1H2zM4 7h8l2 6H2z"/></svg>
      <span>02 9000 0147</span>
    </div>
    <div class="contact" style="left:34px; top:319px;">
      <svg viewBox="0 0 16 16"><path d="M4 1h8v4H4zM1 6h14v6h-3v3H4v-3H1zM5 10v3h6v-3z"/></svg>
      <span>02 9000 0148</span>
    </div>
    <div class="contact" style="left:150px; top:296px;">
      <svg viewBox="0 0 16 16"><path d="M1 3h14v10H1zM2.5 4.5v7.5l4-4zm11 0-4 3.5 4 4zM3 4l5 4.5L13 4z"/></svg>
      <span>sam@brightvale-example.com.au</span>
    </div>
    <div class="contact" style="left:150px; top:319px;">
      <svg viewBox="0 0 16 16"><path d="M8 1a7 7 0 1 0 0 14A7 7 0 0 0 8 1zm-1 2v3H4.2A5 5 0 0 1 7 3zm2 0a5 5 0 0 1 2.8 3H9zM3.1 8H7v2H3.5a5 5 0 0 1-.4-2zM9 8h3.9a5 5 0 0 1-.4 2H9zm-4.6 4H7v1a5 5 0 0 1-2.6-1zm4.6 0h2.6A5 5 0 0 1 9 13z"/></svg>
      <span>https://www.brightvale-example.com.au</span>
    </div>

    <div class="address">
      <svg viewBox="0 0 13 16"><path d="M6.5 0A6 6 0 0 0 .5 6c0 4.5 6 10 6 10s6-5.5 6-10a6 6 0 0 0-6-6zm0 3.5a2.5 2.5 0 1 1 0 5 2.5 2.5 0 0 1 0-5z"/></svg>
      <div>Level 7 214 Marlowe St<br>Sydney NSW 2047</div>
    </div>

    <div class="back-bars"><div class="bar-navy"></div><div class="bar-cyan"></div></div>
  </section>

</main>
</body>
</html>
```